Inspirational Quotes Poster Set

Brookloft is a stylish coworking space, which has a design-oriented vintage look from the 60's with an industrial touch (www.brookloft-example.com) Brookloft Quote Poster Set of 16 posters. The poster should be typo oriented and rather simple. Reflecting a bit the clean billboard design from the sixties. Minimal / simple graphical elements

Target Market(s)

Startups and Entrepreneurs

Industry/Entity Type

Startup

Font styles to use
Sans Serif

Colors

Designer to choose colors to be used in the design.

Requirements
Must have
• Posters need to be on and very stylish

```html
<!DOCTYPE html>
<html lang="en">
<head>
<meta charset="utf-8">
<title>Brookloft Quote Poster Set — Always Challenge the Old Ways</title>
<link href="https://fonts.googleapis.com/css2?family=Inter:wght@700;800&display=swap" rel="stylesheet">
<style>
  :root {
    --page-bg: #e8e5e0;
    --poster-orange: #f0a035;
    --accent-bar: #e5640f;
    --quote-brown: #3a2200;
    --light-text: #ffffff;
  }
  html, body {
    margin: 0;
    padding: 0;
    width: 1200px;
    height: 1200px;
    overflow: hidden;
    background: var(--page-bg);
  }
  .poster {
    position: absolute;
    left: 185px;
    top: 37px;
    width: 830px;
    height: 1125px;
    display: block;
  }
  .poster-bg { fill: var(--poster-orange); }
  .accent-bar { fill: var(--accent-bar); }
  .quote-word {
    font-family: "Inter", sans-serif;
    font-weight: 800;
    font-size: 230px;
    fill: var(--quote-brown);
    fill-opacity: 0.88;
  }
  .attribution {
    font-family: "Inter", sans-serif;
    font-weight: 700;
    font-size: 22px;
    fill: var(--light-text);
    letter-spacing: 0.01em;
  }
  .brand-name {
    font-family: "Inter", sans-serif;
    font-weight: 800;
    font-size: 54px;
    fill: var(--light-text);
  }
</style>
</head>
<body>
  <svg class="poster" viewBox="674 153 878 1190" xmlns="http://www.w3.org/2000/svg" aria-label="Quote poster: always challenge the old ways">
    <defs>
      <clipPath id="poster-area">
        <rect x="674" y="153" width="878" height="1190"/>
      </clipPath>
    </defs>
    <rect class="poster-bg" x="674" y="153" width="878" height="1190"/>

    <g clip-path="url(#poster-area)">
      <rect class="accent-bar" x="808" y="387" width="29" height="696"/>
      <rect class="accent-bar" x="985" y="153" width="30" height="930"/>

      <g class="quote">
        <text class="quote-word" transform="translate(810 1075) rotate(-90)" textLength="665" lengthAdjust="spacingAndGlyphs">always</text>
        <text class="quote-word" transform="translate(995 1075) rotate(-90)" textLength="922" lengthAdjust="spacingAndGlyphs">challenge</text>
        <text class="quote-word" transform="translate(1185 1075) rotate(-90)" textLength="310" lengthAdjust="spacingAndGlyphs">the</text>
        <text class="quote-word" transform="translate(1358 1075) rotate(-90)" textLength="295" lengthAdjust="spacingAndGlyphs">old</text>
        <text class="quote-word" transform="translate(1518 1075) rotate(-90)" textLength="500" lengthAdjust="spacingAndGlyphs">ways</text>
      </g>
    </g>

    <text class="attribution" x="737" y="1177">HAROLD SHELDON,</text>
    <text class="attribution" x="737" y="1207">CEO COPPERBEAN</text>

    <text class="brand-name" x="1253" y="1282" textLength="257" lengthAdjust="spacingAndGlyphs">brookloft</text>
  </svg>
</body>
</html>
```